Business card for medical clinic

I need an upmarket, modern medical/health business card for my clinic

Contact Information for Business Card

name, address, email, qr code

```html
<!DOCTYPE html>
<html lang="en">
<head>
<meta charset="utf-8">
<title>Calvera Health Solutions – Business Card</title>
<link href="https://fonts.googleapis.com/css2?family=Montserrat:wght@400;500;700&display=swap" rel="stylesheet">
<style>
  :root {
    --page-bg: #1c2535;
    --card-white: #ffffff;
    --brand-blue: #1e5f93;
    --accent-blue: #2a9ad8;
    --ink: #1d1d1f;
    --grad-start: #1f3a5c;
    --grad-end: #2599cf;
    --on-dark: #ffffff;
  }
  * { margin: 0; padding: 0; box-sizing: border-box; }
  html, body {
    width: 1200px; height: 900px; overflow: hidden;
    background: var(--page-bg);
    font-family: "Montserrat", Arial, sans-serif;
  }
  .card {
    position: absolute; left: 300px;
    width: 600px; height: 362px;
    border-radius: 16px; overflow: hidden;
  }
  .card--front { top: 57px; background: var(--card-white); }
  .card--back {
    top: 480px;
    background: linear-gradient(135deg, var(--grad-start) 10%, var(--grad-end) 100%);
  }
  .brand {
    position: absolute; display: flex; align-items: center; gap: 22px;
  }
  .card--front .brand { left: 96px; top: 86px; color: var(--brand-blue); }
  .card--back .brand { left: 100px; top: 92px; color: var(--on-dark); }
  .brand__dot {
    width: 26px; height: 26px; border-radius: 50%;
    border: 3px solid currentColor; flex: none;
  }
  .brand__name {
    font-weight: 500; font-size: 34px; line-height: 1.15;
    letter-spacing: 3px; text-transform: uppercase;
  }
  .brand__sub { display: block; font-size: 20px; letter-spacing: 9px; }
  .holder {
    position: absolute; right: 325px; top: 284px; text-align: right;
  }
  .holder__name {
    font-weight: 700; font-size: 23px; color: var(--accent-blue); line-height: 1.1;
  }
  .holder__role { font-size: 13px; color: var(--ink); margin-top: 2px; }
  .divider {
    position: absolute; left: 300px; top: 277px;
    width: 2px; height: 50px; background: var(--accent-blue);
  }
  .contacts {
    position: absolute; left: 320px; top: 276px; list-style: none;
    font-size: 13.5px; color: var(--ink);
  }
  .contacts li { display: flex; align-items: center; gap: 10px; height: 18.5px; }
  .contacts svg { width: 12px; height: 12px; fill: var(--accent-blue); flex: none; }
</style>
</head>
<body>

<section class="card card--front">
  <div class="brand">
    <span class="brand__dot"></span>
    <span class="brand__name">Calvera Health<span class="brand__sub">Solutions</span></span>
  </div>

  <div class="holder">
    <p class="holder__name">Marlon Estevez</p>
    <p class="holder__role">CEO &amp; Founder</p>
  </div>
  <div class="divider"></div>

  <ul class="contacts">
    <li>
      <svg viewBox="0 0 12 12"><path d="M1 4c0-2 2-3 5-3s5 1 5 3v1H8V4H4v1H1zM2 6h8l1 5H1z"/></svg>
      555-014-2290
    </li>
    <li>
      <svg viewBox="0 0 12 12"><path d="M1 2h10v8H1z M1 2l5 4 5-4" stroke="#fff" stroke-width="0.8"/></svg>
      info@calveraclinic.com
    </li>
    <li>
      <svg viewBox="0 0 12 12"><circle cx="6" cy="6" r="5.5"/><path d="M1 6h10M6 .5c-3 3-3 8 0 11M6 .5c3 3 3 8 0 11" stroke="#fff" stroke-width="0.7" fill="none"/></svg>
      www.calveraclinic.com
    </li>
  </ul>
</section>

<section class="card card--back">
  <div class="brand">
    <span class="brand__dot"></span>
    <span class="brand__name">Calvera Health<span class="brand__sub">Solutions</span></span>
  </div>
</section>

</body>
</html>
```